Defense contractor needs a roll-up for an exhibition

The booth we have booked has only a size of 3m².
So this will be the centerpiece of the whole booth.
We need a roll-up that attracts visitors and at the same time it should contain already designed graphics. These graphics are giving visitors an overview of our system. So it is necessary to have them exposed in a height that the booth personal can conveniently point with its fingers at them.
For information about our company and product visit:
https://www.brellowtrackline.com/
For designing you should use Adobe Illustrator and the templates provided in the zip file, to guarantee a perfect print.
I have supplied my business card that you can copy the logo. As the company logo will be already at the booth nearby the top of the roll-up, you should not place it there. It can be in the middle or at the bottom.
I have uploaded a picture of the booth. The roll up will be placed at the left of the screen and has a size of 80cm x 200cm

Defense

Defense

Serif

0054AA
0677BA
7BADD7
CADEEF
E8F1F8

• you must use the Adobe Illustrator template to have a good printing result
• company logo on the upper side of the roll-up

```html
<!DOCTYPE html>
<html lang="en">
<head>
<meta charset="utf-8">
<title>Brellow Trackline – Roll-up</title>
<link rel="stylesheet" href="https://fonts.googleapis.com/css2?family=Roboto+Condensed:ital,wght@0,400;0,700;0,800;1,700;1,800&display=swap">
<style>
  :root {
    --ink: #0b0b0d;
    --white: #ffffff;
    --paper: #ecebf4;
    --sky-top: #0c1f55;
    --sky-mid: #4a4f9a;
    --sky-glow: #c87a8e;
    --sky-horizon: #f0a860;
    --room-light: #dcdbe8;
    --room-mid: #c4c3d3;
    --tick: #1a1a1a;
  }
  * { margin: 0; padding: 0; box-sizing: border-box; }
  html, body { width: 1200px; height: 2480px; overflow: hidden; background: var(--paper); }
  body { font-family: "Roboto Condensed", Arial, sans-serif; color: var(--ink); }

  .rollup { position: relative; width: 1200px; height: 2480px; background: var(--paper); overflow: hidden; }

  .hero-photo {
    position: absolute; left: 0; top: 0; width: 1200px; height: 600px;
    background:
      linear-gradient(180deg, transparent 0 72%, var(--ink) 88% 100%),
      linear-gradient(180deg, var(--sky-top) 0%, var(--sky-mid) 35%, var(--sky-glow) 60%, var(--sky-horizon) 76%);
  }

  .brand-name {
    position: absolute; left: 0; right: 0; top: 90px;
    text-align: center; color: var(--white);
    font-weight: 800; font-size: 68px; letter-spacing: 1px; text-transform: uppercase;
  }

  .title-band { position: absolute; left: 0; top: 560px; width: 1200px; height: 600px; }
  .title-band svg { position: absolute; inset: 0; }
  .title-band h1 {
    position: absolute; left: 60px; right: 60px; top: 70px;
    color: var(--white); text-align: center; text-transform: uppercase;
    font-style: italic; font-weight: 800; font-size: 80px; line-height: 1.12; letter-spacing: 0.5px;
  }

  .training-room {
    position: absolute; left: 160px; top: 1230px; width: 900px; height: 560px;
    background: radial-gradient(ellipse at 55% 45%, var(--room-light) 0%, var(--room-mid) 70%, transparent 100%);
    border-radius: 40px;
  }

  .services { position: absolute; left: 86px; right: 80px; top: 1900px; }
  .services h2 {
    font-weight: 800; font-size: 84px; line-height: 1; display: inline-block;
    padding-bottom: 8px; border-bottom: 5px solid var(--ink);
  }
  .services .lead { margin-top: 34px; font-weight: 700; font-size: 40px; line-height: 1.2; }
  .service-list { list-style: none; margin-top: 14px; }
  .service-list li {
    display: flex; align-items: center; gap: 22px;
    font-size: 40px; line-height: 1.25;
  }
  .service-list svg { width: 36px; height: 36px; flex: none; }
  .services .closing { margin-top: 22px; font-weight: 700; font-size: 38px; }
</style>
</head>
<body>
<main class="rollup">
  <div class="hero-photo" role="img" aria-label="Dusk sky over a battle tank silhouette on grassland"></div>
  <div class="brand-name">Brellow Trackline</div>

  <section class="title-band">
    <svg viewBox="0 0 1200 600" width="1200" height="600" aria-hidden="true">
      <defs>
        <linearGradient id="bandShade" x1="0" y1="0" x2="0" y2="1">
          <stop offset="0" stop-color="#0b0b0d"/>
          <stop offset="1" stop-color="#1d1d22"/>
        </linearGradient>
      </defs>
      <polygon points="0,0 1200,0 1200,480 600,580 0,480" fill="url(#bandShade)"/>
    </svg>
    <h1>Advanced Combat<br>Training Systems for<br>Realistic Combat<br>Simulation</h1>
  </section>

  <div class="training-room" role="img" aria-label="Illustration of a simulation training room with trainee desks facing two large wall displays"></div>

  <section class="services">
    <h2>Services</h2>
    <p class="lead">The signature of the contract is not the end<br>it is just the beginning of a long-lasting partnership.<br>We offer</p>
    <ul class="service-list">
      <li><svg viewBox="0 0 24 24"><circle cx="12" cy="12" r="10" fill="none" stroke="var(--tick)" stroke-width="2"/><path d="M7 12.5l3.2 3.2L17 8.5" fill="none" stroke="var(--tick)" stroke-width="2.4" stroke-linecap="round" stroke-linejoin="round"/></svg>extended warranty programs</li>
      <li><svg viewBox="0 0 24 24"><circle cx="12" cy="12" r="10" fill="none" stroke="var(--tick)" stroke-width="2"/><path d="M7 12.5l3.2 3.2L17 8.5" fill="none" stroke="var(--tick)" stroke-width="2.4" stroke-linecap="round" stroke-linejoin="round"/></svg>logistics support</li>
      <li><svg viewBox="0 0 24 24"><circle cx="12" cy="12" r="10" fill="none" stroke="var(--tick)" stroke-width="2"/><path d="M7 12.5l3.2 3.2L17 8.5" fill="none" stroke="var(--tick)" stroke-width="2.4" stroke-linecap="round" stroke-linejoin="round"/></svg>maintenance contracts</li>
      <li><svg viewBox="0 0 24 24"><circle cx="12" cy="12" r="10" fill="none" stroke="var(--tick)" stroke-width="2"/><path d="M7 12.5l3.2 3.2L17 8.5" fill="none" stroke="var(--tick)" stroke-width="2.4" stroke-linecap="round" stroke-linejoin="round"/></svg>long-term spare part services</li>
    </ul>
    <p class="closing">to keep the equipment in perfect operational condition</p>
  </section>
</main>
</body>
</html>
```